Business Card Design needed for start up company Halvora

In need of a new business card designed for a start up company based in Sydney, Halvora is a new start up innovative Company, our mission it to make property accessible for everyday Australian and to become the leading Real Estate platform in Australia. We want it to be fresh and clean.

Industry/Entity Type

Financial

Contact Information for Business Card

Section for Name
Section for Title

HALVORA - The Strength of Pooling
Mobile:
Direct:

Font styles to use
Sans Serif

Colors
33a6d7
0692cd
0255a3
ffffff

Requirements
Must have
• Logo, all business card details

```html
<!DOCTYPE html>
<html lang="en">
<head>
<meta charset="utf-8">
<title>Halvora Business Card</title>
<link rel="stylesheet" href="https://fonts.googleapis.com/css2?family=Open+Sans:wght@400;600;700&display=swap">
<style>
  :root {
    --navy: #213f78;
    --frost: #e9ebee;
    --frost-edge: #dfe2e6;
    --white: #ffffff;
    --page: #f2f3f5;
  }
  * { margin: 0; padding: 0; box-sizing: border-box; }
  html, body {
    width: 1200px; height: 900px; overflow: hidden;
    background: var(--page);
    font-family: "Open Sans", Arial, sans-serif;
  }
  .card {
    position: absolute; left: 178px; top: 184px;
    width: 845px; height: 533px;
  }
  .card-shape { position: absolute; inset: 0; }
  .brand {
    position: absolute; left: 57px; top: 208px;
    width: 458px; text-align: center;
    color: var(--navy);
  }
  .brand-name {
    font-weight: 700; font-size: 64px; line-height: 1;
    letter-spacing: 1px;
  }
  .tagline {
    margin-top: 46px;
    font-weight: 600; font-size: 20px; line-height: 1.2;
  }
  .person {
    position: absolute; right: 49px; top: 86px;
    text-align: right; color: var(--white);
  }
  .person-name { font-weight: 700; font-size: 30px; line-height: 1.1; }
  .person-title { font-weight: 400; font-size: 21px; margin-top: 2px; }
  .contacts {
    position: absolute; right: 49px; top: 331px;
    list-style: none; color: var(--white);
    font-size: 21px; line-height: 32px;
  }
  .contacts li {
    display: flex; justify-content: flex-end; align-items: center; gap: 10px;
  }
  .contacts svg { width: 20px; height: 20px; fill: var(--white); flex: none; }
</style>
</head>
<body>
  <div class="card">
    <svg class="card-shape" viewBox="0 0 845 533" width="845" height="533">
      <path d="M266.5,0 H845 V533 H266.5 A266.5,266.5 0 0 1 266.5,0 Z" fill="var(--navy)"/>
      <circle cx="286" cy="267" r="229" fill="var(--frost)" stroke="var(--frost-edge)" stroke-width="2"/>
    </svg>

    <div class="brand">
      <p class="brand-name">HALVORA</p>
      <p class="tagline">THE STRENGTH OF POOLING</p>
    </div>

    <div class="person">
      <p class="person-name">MARCUS ELLERY</p>
      <p class="person-title">Managing Director</p>
    </div>

    <ul class="contacts">
      <li>044-987 650 321
        <svg viewBox="0 0 20 20" aria-label="Phone"><path d="M2 7c0-3 3-4 8-4s8 1 8 4v1h-4V6.5c-1-.6-2.5-.8-4-.8s-3 .2-4 .8V8H2z"/><path d="M5 10l2-3h6l2 3v6H5z"/></svg>
      </li>
      <li>044-987 650 321
        <svg viewBox="0 0 20 20" aria-label="Mobile"><path d="M6 1h8a1 1 0 0 1 1 1v16a1 1 0 0 1-1 1H6a1 1 0 0 1-1-1V2a1 1 0 0 1 1-1zm1 3v11h6V4zm3 12.2a1 1 0 1 0 0 1.6 1 1 0 0 0 0-1.6z"/></svg>
      </li>
      <li>hello@halvora.example
        <svg viewBox="0 0 20 20" aria-label="Email"><path d="M2 4h16v1.5l-8 5.5-8-5.5z"/><path d="M2 7.5l8 5.5 8-5.5V16H2z"/></svg>
      </li>
      <li>www.halvora.example
        <svg viewBox="0 0 20 20" aria-label="Website"><circle cx="10" cy="10" r="8.5"/><path d="M6 6c2 0 3 1 2.5 2.5S6 10 7 12s2 3 1 5c-2-1-4-3-4-6 0-2 1-4 2-5zm6-3c1 1 0 2 1 3s3 0 3 2-2 2-2 4 1 3 0 4c-1-1-2-2-2-4s-2-2-2-4 1-4 2-5z" fill="var(--navy)"/></svg>
      </li>
    </ul>
  </div>
</body>
</html>
```